Business Card Design Project

We need a Business Card for an Mechanical Engineering firm in Singapore. The design should be Modern & Technical looking, yet eye catching.

Our company deals in Cutting Tools & Machine Accessories for the Manufacturing Industries such as Oil & Gas, Aero Space, etc... For more information on our Company, you can either email me or view our website www.torvalen.com.sg.

We are trying to revamp our image to give our consumers a fresh new perspective to our company, so we welcome all ideas.

Industry/Entity Type

Business

Requirements
Must have
• Must incorporate New Company Logo into the card as shown in Uploaded file.

```html
<!DOCTYPE html>
<html lang="en">
<head>
<meta charset="utf-8">
<title>Torvalen Tools – Business Card</title>
<link href="https://fonts.googleapis.com/css2?family=Barlow+Condensed:wght@300;400;500&display=swap" rel="stylesheet">
<style>
  :root {
    --paper: #ffffff;
    --steel-dark: #2a2a2a;
    --steel-mid: #6e6e6e;
    --steel-light: #e4e4e4;
    --panel-black: #000000;
    --panel-glow: #8d8d8d;
    --panel-haze: #4a4a4a;
    --text-light: #f2f2f2;
    --text-soft: #dcdcdc;
    --logo-grey: #cfcfcf;
  }
  * { margin: 0; padding: 0; box-sizing: border-box; }
  html, body {
    width: 1200px; height: 846px; overflow: hidden;
    background: var(--paper);
  }
  .canvas { position: relative; width: 1200px; height: 846px; }

  .card {
    position: absolute;
    width: 486px; height: 316px;
    background:
      linear-gradient(90deg, var(--steel-dark) 0%, var(--steel-mid) 25%, var(--steel-light) 50%, var(--steel-mid) 75%, var(--steel-dark) 100%);
    box-shadow: 4px 6px 8px rgba(0,0,0,0.35);
  }
  .card::before {
    content: ""; position: absolute; inset: 0;
    background: linear-gradient(180deg, rgba(255,255,255,0.15) 0%, rgba(0,0,0,0.25) 50%, rgba(255,255,255,0.12) 100%);
  }
  .card--front { left: 77px; top: 70px; }
  .card--back  { left: 608px; top: 404px; }

  .card__panel {
    position: absolute;
    left: 20px; top: 20px; right: 20px; bottom: 24px;
    background: radial-gradient(ellipse 48% 62% at 50% 46%, var(--panel-glow) 0%, var(--panel-haze) 55%, var(--panel-black) 100%);
    box-shadow: inset 0 0 3px rgba(0,0,0,0.9);
  }
  .card--front .card__panel {
    clip-path: polygon(0 0, 100% 0, 100% 68%, 90.5% 100%, 0 100%);
  }
  .card--back .card__panel {
    clip-path: polygon(0 0, 100% 0, 100% 100%, 12% 100%, 0 76%);
    background: radial-gradient(ellipse 48% 62% at 50% 48%, var(--panel-glow) 0%, var(--panel-haze) 55%, var(--panel-black) 100%);
  }

  .brand {
    position: absolute; left: 0; right: 0; top: 108px;
    display: flex; align-items: center; justify-content: center; gap: 12px;
    font-family: "Barlow Condensed", "Arial Narrow", sans-serif;
    font-weight: 300; font-size: 46px; letter-spacing: 1px;
    color: var(--logo-grey);
  }
  .brand__dot {
    width: 34px; height: 34px; border-radius: 50%;
    background: var(--logo-grey);
  }

  .contact {
    position: absolute; left: 0; right: 0; top: 62px;
    text-align: center;
    font-family: "Barlow Condensed", "Arial Narrow", sans-serif;
    color: var(--text-light);
    text-shadow: 0 0 6px rgba(0,0,0,0.6);
    line-height: 1;
  }
  .contact__name  { font-size: 28px; font-weight: 500; letter-spacing: 0.5px; }
  .contact__role  { font-size: 17px; font-weight: 500; margin-top: 3px; color: var(--text-soft); }
  .contact__line  { font-size: 14px; font-weight: 400; margin-top: 4px; color: var(--text-soft); }
  .contact__line--first { margin-top: 10px; }
  .contact__site  { font-size: 31px; font-weight: 500; margin-top: 14px; }
</style>
</head>
<body>
<main class="canvas">
  <section class="card card--front" aria-label="Card front">
    <div class="card__panel">
      <div class="brand">
        <span class="brand__dot" aria-hidden="true"></span>
        <span class="brand__name">TORVALEN TOOLS</span>
      </div>
    </div>
  </section>

  <section class="card card--back" aria-label="Card back">
    <div class="card__panel">
      <div class="contact">
        <p class="contact__name">MARISOL VANTEK</p>
        <p class="contact__role">GRAPHIC DESIGNER</p>
        <p class="contact__line contact__line--first">0000 000 000 000</p>
        <p class="contact__line">THIS IS YOUR STREET&nbsp; THIS IS YOUR STREET</p>
        <p class="contact__line">THIS IS YOUR EMAIL</p>
        <p class="contact__site">THIS IS YOUR SITE</p>
      </div>
    </div>
  </section>
</main>
</body>
</html>
```